Frostvale Harborline LLC

we need a business card design

Industry/Entity Type

hvac

Contact Information for Business Card

my logo

Requirements
Must have
• my logo and same colors

```html
<!DOCTYPE html>
<html lang="en">
<head>
<meta charset="utf-8">
<title>Frostvale Harborline LLC — Business Card</title>
<link rel="stylesheet" href="https://fonts.googleapis.com/css2?family=Montserrat:wght@400;500;700;800&display=swap">
<style>
  :root {
    --stage: #ececec;
    --brand-blue: #1f63b8;
    --brand-blue-deep: #174f98;
    --brand-blue-light: #2a73c9;
    --brand-gold: #f2b24a;
    --card-white: #ffffff;
    --ink: #2b2b2b;
    --name-blue: #2a6fc0;
    --faint: #eef1f6;
  }
  * { margin: 0; padding: 0; box-sizing: border-box; }
  html, body { width: 1200px; height: 913px; overflow: hidden; }
  body {
    background: var(--stage);
    font-family: "Montserrat", sans-serif;
    position: relative;
  }
  .card {
    position: absolute;
    width: 520px;
    height: 297px;
    top: 308px;
    border-radius: 4px;
    overflow: hidden;
    box-shadow: 0 6px 18px rgba(0,0,0,.18);
  }
  .card-front { left: 40px; background: var(--brand-blue); }
  .card-back { left: 640px; background: var(--card-white); }

  .front-pattern {
    position: absolute; inset: 0;
    background: linear-gradient(135deg, var(--brand-blue-light), var(--brand-blue) 55%, var(--brand-blue-deep));
  }
  .front-brand {
    position: absolute; inset: 0;
    display: flex; align-items: center; justify-content: center; gap: 14px;
  }
  .brand-dot {
    width: 18px; height: 18px; border-radius: 50%;
    background: var(--brand-gold);
  }
  .brand-name {
    font-weight: 800; font-size: 28px; color: var(--card-white);
    letter-spacing: .5px;
  }

  .back-decoration {
    position: absolute; right: 0; top: 90px;
    width: 230px; height: 207px;
    background: radial-gradient(ellipse at 60% 50%, var(--faint), rgba(238,241,246,0) 70%);
  }
  .back-brand {
    position: absolute; right: 28px; top: 30px;
    display: flex; align-items: center; gap: 8px;
  }
  .back-brand .brand-dot { width: 11px; height: 11px; }
  .back-brand .brand-name { font-size: 15px; color: var(--brand-blue); }

  .address {
    position: absolute; right: 28px; top: 96px;
    text-align: right; font-size: 11px; line-height: 1.45; color: var(--ink);
  }
  .person { position: absolute; left: 30px; top: 120px; }
  .person-name { font-weight: 700; font-size: 19px; color: var(--name-blue); }
  .person-role { font-size: 11px; color: var(--ink); margin-top: 2px; }

  .contacts {
    position: absolute; left: 30px; bottom: 26px;
    list-style: none; font-size: 11px; color: var(--ink);
  }
  .contacts li { display: flex; align-items: center; gap: 9px; line-height: 1.7; }
  .contacts svg { width: 11px; height: 11px; flex: none; }
</style>
</head>
<body>
  <section class="card card-front">
    <div class="front-pattern" role="img" aria-label="Repeating faint brand pattern on blue background"></div>
    <div class="front-brand">
      <span class="brand-dot"></span>
      <span class="brand-name">Frostvale Harborline LLC</span>
    </div>
  </section>

  <section class="card card-back">
    <div class="back-decoration" role="img" aria-label="Faint large brand decoration"></div>
    <div class="back-brand">
      <span class="brand-dot"></span>
      <span class="brand-name">Frostvale Harborline LLC</span>
    </div>
    <p class="address">48 Quay Lane,<br>Lakeview, NY 10000</p>
    <div class="person">
      <h1 class="person-name">Dana Whitfield</h1>
      <p class="person-role">Managing Director</p>
    </div>
    <ul class="contacts">
      <li>
        <svg viewBox="0 0 12 12"><path d="M3 1h2l1 3-1.5 1a6 6 0 0 0 2.5 2.5L8 6l3 1v2a2 2 0 0 1-2 2A8 8 0 0 1 1 3a2 2 0 0 1 2-2z" fill="none" stroke="#f2b24a" stroke-width="1.2"/></svg>
        +1 (555) 010-4827
      </li>
      <li>
        <svg viewBox="0 0 12 12"><rect x="1" y="2.5" width="10" height="7" fill="#f2b24a"/><path d="M1 2.5l5 4 5-4" fill="none" stroke="#fff" stroke-width="1"/></svg>
        info@frostvaleharbor.com
      </li>
      <li>
        <svg viewBox="0 0 12 12"><circle cx="6" cy="6" r="4.5" fill="none" stroke="#f2b24a" stroke-width="1.2"/><path d="M1.5 6h9M6 1.5c-2 2.5-2 6.5 0 9M6 1.5c2 2.5 2 6.5 0 9" fill="none" stroke="#f2b24a" stroke-width="1"/></svg>
        www.frostvaleharbor.com
      </li>
    </ul>
  </section>
</body>
</html>
```